e-commerce store for sport clothing online store "baseball merchandise "web application...

I want to design a UX/UI for my web application website for the online store I will provide you with the following:
1. screen shots of the initial design for the pages>
2. the logo files.
3. The brand guideline file.

the provided files (screen shots) is guideline I want to see CREATIVITY with the UX/UI DESIGN.
PS. PLEASE FOLLOW THE BRANDGUIDE LINE CAREFULLY SPECIALLY THE TYPOGRAPHY & THE COLOR CODES.

PLEASE VISIT THIS WEBSITE brightlane.varomi-qz.com to see more for the screens.

```html
<!DOCTYPE html>
<html lang="en">
<head>
<meta charset="UTF-8">
<title>Checkout – Shipping Details</title>
<link href="https://fonts.googleapis.com/css2?family=Lato:wght@400;700;900&display=swap" rel="stylesheet">
<style>
  :root {
    --navy: #13284c;
    --white: #ffffff;
    --canvas-bg: #eceef2;
    --ink: #111111;
    --muted: #555555;
    --field-border: #333333;
    --button-grey: #9c9c9c;
  }
  * { box-sizing: border-box; margin: 0; padding: 0; }
  html, body {
    width: 850px; height: 1200px; overflow: hidden;
    background: var(--canvas-bg);
    font-family: "Lato", Arial, sans-serif;
    color: var(--ink);
  }
  .screen {
    position: absolute; left: 155px; top: 0;
    width: 540px; height: 1200px;
    background: var(--white); overflow: hidden;
  }
  .app-bar {
    position: absolute; left: 0; top: 0; width: 100%; height: 122px;
    background: var(--navy); z-index: 2;
  }
  .back-button { position: absolute; left: 36px; top: 48px; width: 30px; height: 30px; }
  .app-title {
    position: absolute; left: 0; right: 0; top: 46px; text-align: center;
    color: var(--white); font-weight: 700; font-size: 26px;
  }
  .stepper-labels { position: absolute; left: 0; top: 122px; width: 100%; height: 10px; overflow: hidden; }
  .step-label {
    position: absolute; top: -12px; width: 120px; margin-left: -60px; text-align: center;
    color: var(--navy); font-size: 18px;
  }
  .section-title { position: absolute; left: 21px; font-weight: 700; font-size: 23px; }
  .field {
    position: absolute; height: 70px;
    border: 1.5px solid var(--field-border); border-radius: 4px;
    padding: 0 14px;
  }
  .field.half-left { left: 21px; width: 237px; }
  .field.half-right { left: 281px; width: 236px; }
  .field.full { left: 21px; width: 496px; }
  .field-label { display: block; font-size: 16px; color: var(--muted); margin-top: 8px; }
  .field-value { display: block; font-size: 22px; color: var(--ink); margin-top: 0; }
  .field-placeholder { display: block; font-size: 22px; color: var(--muted); line-height: 67px; }
  .default-row {
    position: absolute; left: 21px; width: 496px; top: 958px;
    display: flex; justify-content: space-between; align-items: center;
    font-weight: 700; font-size: 19px;
  }
  .toggle {
    width: 34px; height: 19px; border-radius: 10px; background: var(--navy); position: relative;
  }
  .toggle::after {
    content: ""; position: absolute; right: 6px; top: 5.5px;
    width: 8px; height: 8px; border-radius: 50%; background: var(--white);
  }
  .action-bar {
    position: absolute; left: 6px; right: 6px; top: 1100px; bottom: 0;
    background: var(--white); border-radius: 14px 14px 0 0;
    box-shadow: 0 -4px 10px rgba(0,0,0,0.12);
  }
  .proceed-button {
    position: absolute; left: 12px; right: 12px; top: 14px; height: 66px;
    background: var(--button-grey); border: none; border-radius: 4px;
    color: var(--white); font-family: "Lato", Arial, sans-serif; font-weight: 700; font-size: 21px;
  }
</style>
</head>
<body>
  <main class="screen">
    <header class="app-bar">
      <svg class="back-button" viewBox="0 0 30 30" aria-label="Back">
        <path d="M26 15H5M13 6l-9 9 9 9" fill="none" stroke="#ffffff" stroke-width="2.8" stroke-linecap="round" stroke-linejoin="round"/>
      </svg>
      <h1 class="app-title">Checkout</h1>
    </header>

    <div class="stepper-labels">
      <span class="step-label" style="left:117px">Details</span>
      <span class="step-label" style="left:267px">Details</span>
    </div>

    <h2 class="section-title" style="top:172px">Deliver to</h2>
    <div class="field half-left" style="top:224px">
      <span class="field-label">First Name*</span><span class="field-value">Remy</span>
    </div>
    <div class="field half-right" style="top:224px">
      <span class="field-label">Last Name*</span><span class="field-value">Castell</span>
    </div>
    <div class="field full" style="top:318px">
      <span class="field-label">Phone*</span><span class="field-value">55819027xx</span>
    </div>

    <h2 class="section-title" style="top:435px">Shipping Address</h2>
    <div class="field full" style="top:485px"><span class="field-placeholder">Area*</span></div>
    <div class="field half-left" style="top:581px"><span class="field-placeholder">Block*</span></div>
    <div class="field half-right" style="top:581px"><span class="field-placeholder">Street*</span></div>
    <div class="field half-left" style="top:675px"><span class="field-placeholder">Avenue</span></div>
    <div class="field half-right" style="top:675px"><span class="field-placeholder">Building</span></div>
    <div class="field half-left" style="top:771px"><span class="field-placeholder">Floor</span></div>
    <div class="field half-right" style="top:771px"><span class="field-placeholder">Appartment</span></div>
    <div class="field full" style="top:866px"><span class="field-placeholder">Map Location</span></div>

    <div class="default-row">
      <span>Default Shipping Address</span>
      <span class="toggle" role="switch" aria-checked="true"></span>
    </div>

    <footer class="action-bar">
      <button class="proceed-button" type="button">Proceed</button>
    </footer>
  </main>
</body>
</html>
```